Business card design for a dynamic IT consulting company

We need a business card design for a young firm, specialized in the Telecommunications/Consulting industry. The name of the company is Quindor and Partners Business Consulting Ltd. (Short name: Quindor and Partnes)
Quindor = solve read reverse, so we aim to be uncomplicated and solution-oriented. The small pipe in our logo is also related to the word solve. So we need a new business card design, which is simple, eye catching and something non traditional (I would probably prefer a square shaped design rather than a rectangle, but open for suggestions). Attached our logo.

Target Market(s)

Usually our customers are Tier1 Telecoms providers (Q-Netra, Palorix, etc) and their executives.

Industry/Entity Type

Business

Contact Information for Business Card

Name: Bence Tolnavari
Email: b.tolnavari@quindor.hu
Web: www.quindor.hu
Mobile: +36 30 518 2769
Title: Managing Director

Optional:
Company name: Quindor and Partners Ltd.
Address: 1087 Budapest, Tolvenka str. 28/C, Hungary

Font styles to use
Other font styles liked:
• helveticaneue_medium, Prime Regular are used now.

Colors

Designer to choose colors to be used in the design.

Requirements
Must have
• I would like to have a 2 sided design.
Nice to have
• I thought if we make the logo a bit bigger (without the company name), that could go to the back with the company name below. I though, if the pipe in the logo is somehow touchable on the business card, would be nice and unique.

```html
<!DOCTYPE html>
<html lang="en">
<head>
<meta charset="utf-8">
<title>Quindor and Partners – Business Card</title>
<link rel="stylesheet" href="https://fonts.googleapis.com/css2?family=Arimo:wght@400;700&display=swap">
<style>
  :root {
    --backdrop: #e3e3e3;
    --card: #f4f4f4;
    --band: #5b5b5d;
    --ink: #505052;
    --cyan: #0e9ad7;
    --magenta: #b0288f;
    --white: #ffffff;
  }
  * { margin: 0; padding: 0; box-sizing: border-box; }
  html, body {
    width: 1200px; height: 960px; overflow: hidden;
    background: var(--backdrop);
    font-family: "Arimo", Helvetica, Arial, sans-serif;
  }
  .sheet { position: relative; width: 1200px; height: 960px; }
  .card {
    position: absolute; top: 305px; width: 343px; height: 343px;
    background: var(--card);
    box-shadow: 1px 2px 3px rgba(0,0,0,0.35);
  }
  .card--front { left: 200px; }
  .card--back { left: 651px; }

  /* front */
  .front-band {
    position: absolute; left: 0; top: 0; width: 100%; height: 95px;
    background: var(--band);
    display: flex; align-items: center; justify-content: center; gap: 10px;
  }
  .brand-mark { width: 12px; height: 12px; background: var(--cyan); }
  .brand-name { color: var(--white); font-size: 24px; font-weight: 400; letter-spacing: -0.2px; }
  .stripes { position: absolute; top: 97px; left: 0; width: 100%; height: 3px; display: flex; gap: 3px; }
  .stripes span { flex: 1; }
  .stripe--grey { background: var(--band); }
  .stripe--magenta { background: var(--magenta); }
  .stripe--cyan { background: var(--cyan); }

  .contact { position: absolute; top: 136px; left: 0; width: 100%; text-align: center; color: var(--ink); }
  .contact__name { color: var(--cyan); font-size: 19px; font-weight: 700; line-height: 22px; }
  .contact__title { font-size: 16px; line-height: 20px; letter-spacing: 0.3px; }
  .contact__address { margin-top: 8px; font-size: 14px; line-height: 18.5px; }
  .contact__lines { margin-top: 9px; font-size: 14px; line-height: 18.5px; }
  .contact__line { display: flex; align-items: center; justify-content: center; gap: 3px; }
  .contact__line svg { width: 11px; height: 11px; fill: var(--cyan); }

  /* back */
  .back-brand {
    position: absolute; top: 188px; left: 0; width: 100%;
    display: flex; align-items: center; justify-content: center; gap: 10px;
  }
  .back-brand .brand-mark { width: 14px; height: 14px; background: var(--magenta); }
  .back-brand .brand-name { color: var(--ink); font-size: 30px; }
  .back-web {
    position: absolute; top: 293px; left: 0; width: 100%; text-align: center;
    color: var(--ink); font-size: 13px; letter-spacing: 7px;
  }
</style>
</head>
<body>
<main class="sheet">
  <section class="card card--front">
    <header class="front-band">
      <span class="brand-mark"></span>
      <span class="brand-name">Quindor &amp; Partners</span>
    </header>
    <div class="stripes">
      <span class="stripe--grey"></span>
      <span class="stripe--magenta"></span>
      <span class="stripe--cyan"></span>
    </div>
    <div class="contact">
      <p class="contact__name">BENCE TOLNAVARI</p>
      <p class="contact__title">MANAGING DIRECTOR</p>
      <p class="contact__address">Quindor and Partners Ltd.<br>1087 Budapest<br>Tolvenka str. 28/C, Hungary</p>
      <div class="contact__lines">
        <p class="contact__line">
          <svg viewBox="0 0 12 12" aria-hidden="true"><path d="M3 0h6a1 1 0 0 1 1 1v10a1 1 0 0 1-1 1H3a1 1 0 0 1-1-1V1a1 1 0 0 1 1-1zm0.5 1.5v8h5v-8z"/></svg>
          +36 30 518 2769
        </p>
        <p class="contact__line">
          <svg viewBox="0 0 12 12" aria-hidden="true"><path d="M0 2h12v8H0zM1 3l5 3.5L11 3v-0.2H1z" fill-rule="evenodd"/></svg>
          b.tolnavari@quindor.hu
        </p>
        <p class="contact__line">
          <svg viewBox="0 0 12 12" aria-hidden="true"><circle cx="6" cy="6" r="5.5"/></svg>
          www.quindor.hu
        </p>
      </div>
    </div>
  </section>

  <section class="card card--back">
    <div class="back-brand">
      <span class="brand-mark"></span>
      <span class="brand-name">Quindor &amp; Partners</span>
    </div>
    <p class="back-web">www.quindor.hu</p>
  </section>
</main>
</body>
</html>
```